Visitenkarten und Briefpapier
Zielgruppe
Planung und Realisierung von individuellen und wertbeständigen Kamin- und Ofenlösungen, sowie Fliesen- und Baddesign.
Aufgabenstellung
Wir benötigen ein möglichst schlichtes Design für Visitenkarten, bzw. Briefpapier. Für die Visitenkarten gerne auch Vorschläge mit Prägung, Ausstanzung oder mit Heißfolie. Auch Klappkarten wären denkbar. Das Design soll "das gewisse Etwas haben" und nicht zu verspielt sein.
Die Visitenkarten sind für die Firma KORVA, das Logo von der Ausstellung "raumfunke" soll dezent mit eingebunden werden (bei dem Briefpapier z.B. in der Fußzeile". Die farbliche Gestaltung sollte sich an den Farben des Logos orientieren.
Schriftart für Texte: Century Gothic
Schriftfarbe: RAL 7016
Nur eine Idee: Ich könnte mir auch gut vorstellen, dass die Visitenkarte aus einer Zündholzverpackung (wenn dann aber eine besondere mit nur einem Zündholz oder einem besonders breiten) besteht: http://glimmvelo.de/produkte_briefchen.php

```html
<!DOCTYPE html>
<html lang="de">
<head>
<meta charset="utf-8">
<title>KORVA – Visitenkarte</title>
<link href="https://fonts.googleapis.com/css2?family=Questrial&display=swap" rel="stylesheet">
<style>
  :root {
    --backdrop: #c89e6a;
    --anthracite: #25353b;
    --flame: #f0880a;
    --paper: #ffffff;
    --ink: #1e1e1e;
    --muted: #8d9396;
    --card-w: 603px;
    --card-h: 390px;
  }
  * { margin: 0; padding: 0; box-sizing: border-box; }
  html, body {
    width: 1200px;
    height: 1120px;
    overflow: hidden;
    background: var(--backdrop);
    font-family: "Questrial", "Century Gothic", sans-serif;
  }
  .card {
    position: absolute;
    left: 271px;
    width: var(--card-w);
    height: var(--card-h);
  }
  .card--front { top: 120px; background: var(--paper); }
  .card--back { top: 571px; background: var(--anthracite); }

  .contact-panel {
    position: absolute;
    left: 0; top: 0;
    width: 245px;
    height: 100%;
    background: var(--anthracite);
    color: #f2f2f2;
  }
  .brand-mark {
    position: absolute;
    color: var(--flame);
    text-align: center;
    white-space: nowrap;
  }
  .brand-mark--panel {
    left: 0;
    width: 245px;
    top: 104px;
    font-size: 46px;
    line-height: 50px;
    letter-spacing: 2px;
  }
  .brand-mark--back {
    left: 0;
    width: 100%;
    top: 136px;
    font-size: 88px;
    line-height: 92px;
    letter-spacing: 4px;
  }
  .contact {
    position: absolute;
    left: 18px;
    top: 270px;
    font-size: 18px;
    line-height: 20.5px;
    font-style: normal;
  }
  .contact .mail { margin-top: 6px; }
  .contact .label { display: inline-block; width: 45px; }

  .brand {
    position: absolute;
    right: 30px;
    top: 14px;
    text-align: right;
    color: var(--ink);
  }
  .brand-name {
    font-size: 74px;
    line-height: 74px;
    letter-spacing: 2px;
  }
  .brand-tagline {
    font-size: 22px;
    line-height: 24px;
    margin-top: -4px;
  }
  .person {
    position: absolute;
    right: 28px;
    top: 175px;
    text-align: right;
  }
  .person-name {
    font-size: 35px;
    line-height: 40px;
    color: var(--anthracite);
  }
  .person-role {
    font-size: 16px;
    line-height: 20px;
    color: var(--flame);
  }
  .website {
    position: absolute;
    right: 26px;
    bottom: 12px;
    font-size: 18px;
    color: var(--anthracite);
  }
  .showroom-name {
    position: absolute;
    right: 17px;
    bottom: 18px;
    font-size: 21px;
    color: var(--muted);
  }
</style>
</head>
<body>
  <section class="card card--front" aria-label="Vorderseite">
    <div class="contact-panel">
      <div class="brand-mark brand-mark--panel">KORVA</div>
      <address class="contact">
        <div>Am Lindenhang 12</div>
        <div>34590 Wendbach</div>
        <div><span class="label">fon:</span>05672 / 41 38 20</div>
        <div><span class="label">fax:</span>05672 / 41 38 28</div>
        <div class="mail">info@korva-wendbach.de</div>
      </address>
    </div>
    <div class="brand">
      <div class="brand-name">KORVA</div>
      <div class="brand-tagline">kamine · öfen · fliesen</div>
    </div>
    <div class="person">
      <div class="person-name">Jonas Korvel</div>
      <div class="person-role">Geschäftsführer</div>
    </div>
    <div class="website">www.korva-wendbach.de</div>
  </section>

  <section class="card card--back" aria-label="Rückseite">
    <div class="brand-mark brand-mark--back">KORVA</div>
    <div class="showroom-name">raumfunke</div>
  </section>
</body>
</html>
```